Counseling Practice Business Card

I need a professional looking business card incorporating my new logo that was just completed. Card needs to incorporate my name and title, description of my specialty, my address, my phone number, my fax number, my email and my website URL. I need to be able to choose design on/with different paper colors and textures.
I do not have a lot of business card ideas so I am open to anything but I want bold,sharp, clear card without additional designs other than my logo (see attached file info). I am open to different color backgrounds or paper colors including black. I do not like traditional brackets around area codes in phone number or dashes between numbers in phone number. Am open to other ways of presenting including periods between numbers as appropriate. I do not know enough to know what I like yet but I want card to coordinate and work together with my logo. My practice emphasizes natural mental health interventions so any use of color (with background paper color or the blue and green in my logo) that elicits nature is nice. In addition to black, any natural brown or wood looking background might be desirable also. Most of the offerings so far look very similar and boring.

Target Market(s)

Potential therapy clients and other professionals

Contact Information for Business Card

Card information:
Gerald M. Whitcombe, Ph.D.
Licensed Clinical Psychologist
Integrative Health Coach
4812 Marlowe Ridge Blvd SE
Suite 310
Duluth, GA 30096
(770) 415-2983 phone
(770) 581-4096 fax
drgeraldwhitcombe@quillmarsh.net
brightfernwellness.net

Font styles to use
Serif
Sans Serif
Other font styles liked:
• anything that you think looks crisp, clear and easily readable

Requirements
Must have
• Any color used should coordinate with my logo design (see attached files).
• Card should be printed horizontally so top and bottom are longest sides of rectangle.
• Background color or paper color should complement and highlight logo. Do not like a white background. black, grey, brown or any color my logo would blend well with.
Nice to have
• I would like designer to utilize color to highlight letters/name or phone-fax-web symbols.
• Bottom edge of card could be highlighted if appropriate to an idea.
Should not have
• I would NOT want the card to have a pure white background at all.
• No clear cards.
• Cards should be oriented with long sides on bottom and top, NOT sides. DO NOT LIKE THIS THIN TALL ORIENTATION.

```html
<!DOCTYPE html>
<html lang="en">
<head>
<meta charset="utf-8">
<title>Brightfern Wellness – Business Card</title>
<link href="https://fonts.googleapis.com/css2?family=Roboto:wght@400;500;700&display=swap" rel="stylesheet">
<style>
  :root {
    --backdrop: #3a3b3d;
    --card: #1f2022;
    --emboss: #7d7f83;
    --brand-blue: #2f7fc6;
    --brand-green: #1f7a3a;
    --ink-light: #eceef0;
  }
  * { margin: 0; padding: 0; box-sizing: border-box; }
  html, body {
    width: 799px; height: 1200px; overflow: hidden;
    background: var(--backdrop);
    font-family: "Roboto", Arial, sans-serif;
  }
  .sheet {
    position: relative; width: 799px; height: 1200px;
    display: flex; flex-direction: column; align-items: center;
    justify-content: space-around; padding: 60px 0;
  }
  .card {
    position: relative; width: 620px; height: 354px;
    background: var(--card); overflow: hidden;
    box-shadow: 0 14px 30px rgba(0,0,0,.45);
  }
  /* Front */
  .card--front { display: flex; align-items: center; justify-content: center; }
  .brand-front {
    font-weight: 700; font-size: 54px; letter-spacing: 1px;
    color: var(--emboss); text-align: center; line-height: 1.05;
  }
  /* Back */
  .brand-back {
    position: absolute; left: 36px; top: 34px;
    font-weight: 700; font-size: 32px; line-height: 1.05;
    color: var(--brand-blue);
  }
  .identity { position: absolute; left: 36px; top: 172px; }
  .identity__name { font-weight: 700; font-size: 22px; color: var(--brand-blue); }
  .identity__title { font-size: 12px; color: var(--ink-light); margin-top: 4px; }
  .contact {
    position: absolute; left: 360px; top: 188px;
    font-size: 14px; color: var(--ink-light); line-height: 1.35;
  }
  .contact__row { display: flex; align-items: center; gap: 8px; }
  .contact__row svg { width: 12px; height: 12px; fill: var(--brand-blue); flex: none; }
  .contact__row .icon-line { fill: none; stroke: var(--brand-blue); stroke-width: 1.4; }
  .contact__address { margin-bottom: 4px; }
  .band-green {
    position: absolute; left: 0; right: 0; bottom: 0; height: 16px;
    background: var(--brand-green);
  }
  .band-blue {
    position: absolute; left: 320px; right: 0; bottom: 0; height: 58px;
    background: var(--brand-blue); border-top-left-radius: 40px;
    display: flex; align-items: center; padding-left: 36px;
    font-size: 15px; color: var(--ink-light);
  }
</style>
</head>
<body>
<main class="sheet">
  <section class="card card--front" aria-label="Card front">
    <div class="brand-front">Brightfern<br>Wellness</div>
  </section>

  <section class="card card--back" aria-label="Card back">
    <div class="brand-back">Brightfern<br>Wellness</div>
    <div class="identity">
      <div class="identity__name">John Doe Smith</div>
      <div class="identity__title">Managing Director</div>
    </div>
    <div class="contact">
      <div class="contact__address">234 Anywhere St., Any City,<br>Any Town, US 123456</div>
      <div class="contact__row">
        <svg viewBox="0 0 12 12" aria-hidden="true"><path d="M2.5 1l2 2-1 1.5c.8 1.6 2 2.8 3.5 3.5L8.5 7l2 2-1.2 1.6C5 10.2 1.8 7 1 2.2z"/></svg>
        <span>555.014.2738</span>
      </div>
      <div class="contact__row">
        <svg viewBox="0 0 12 12" aria-hidden="true"><rect x="3" y="1" width="6" height="3"/><rect x="1" y="4.5" width="10" height="5" rx="1"/><rect x="3" y="8" width="6" height="3"/></svg>
        <span>555.014.2791</span>
      </div>
      <div class="contact__row">
        <svg viewBox="0 0 12 12" aria-hidden="true"><path class="icon-line" d="M1 2.5h10v7H1z M1 2.5l5 4 5-4"/></svg>
        <span>yourname@yourwebsite.com</span>
      </div>
    </div>
    <div class="band-green"></div>
    <div class="band-blue">www.yourwebsite.com</div>
  </section>
</main>
</body>
</html>
```